Brand new letterhead, business card, email signature etc.

We are a financial company in London, UK. Our website is www.marlowvane.com. We're wanting a complete remodel of the company colours, letter head, business cards, email signatures, etc. Looking to keep the same font for the company name. I have upload a colour palette that we want to work with. We're looking for company letterhead for outgoing letters/ correspondence, letterhead for internal documentation, email signatures, e-letters. etc. Ultimately we will redesign the entire website also. It is important that our clients get a strong, secure, warm, trustworthy, solid feeling and first impression.
Updates

Designs look the same

Target Market(s)

Institutional investors, (ultra) high net worth individuals

Industry/Entity Type

Finance, Invesments banking.

Font styles to use
Other font styles liked:
• Current font is "Champagne & Limousines"

Requirements
Must have
• Must use the colours provided on the PDF uploaded to the portal. The purple = main colour. The red = accent colour.
Nice to have
• Nice to use same font as now for the company name "Corvane". Font is "Champagne & Limousines". Nice to have some reference to the old logo flower, but only subtle.
Should not have
• Do not use the colour red from our website. Use the colours provided on the colour palette PDF that I uploaded in the portal.

```html
<!DOCTYPE html>
<html lang="en">
<head>
<meta charset="utf-8">
<title>Corvane — Business Card</title>
<link rel="stylesheet" href="https://fonts.googleapis.com/css2?family=Josefin+Sans:wght@300&family=Jost:wght@400;500&display=swap">
<style>
  :root {
    --backdrop: #2e2e2e;
    --card-top: #ffffff;
    --card-bottom: #e4e4e4;
    --plum: #2a0b1d;
    --accent-red: #d2331d;
    --ink: #1f1a1c;
    --ink-soft: #3a3336;
  }
  * { margin: 0; padding: 0; box-sizing: border-box; }
  html, body { width: 1200px; height: 900px; overflow: hidden; }
  body {
    background: var(--backdrop);
    display: flex;
    align-items: center;
    justify-content: center;
    gap: 60px;
  }
  .card {
    position: relative;
    width: 330px;
    height: 540px;
    background: linear-gradient(160deg, var(--card-top) 20%, var(--card-bottom) 100%);
    box-shadow: 0 8px 24px rgba(0,0,0,0.45);
    overflow: hidden;
  }
  .wordmark {
    font-family: "Josefin Sans", "Century Gothic", sans-serif;
    font-weight: 300;
    color: var(--ink);
    letter-spacing: 0.22em;
    text-transform: uppercase;
  }
  .card-front .wordmark {
    position: absolute;
    top: 50%;
    left: 0;
    right: 0;
    text-align: center;
    transform: translateY(-50%);
    font-size: 30px;
    padding-left: 0.22em;
  }
  .card-back .side-band {
    position: absolute;
    top: 0; bottom: 0; left: 0;
    width: 44px;
    background: var(--plum);
  }
  .card-back .side-stripe {
    position: absolute;
    top: 0; bottom: 0; left: 44px;
    width: 7px;
    background: var(--accent-red);
  }
  .card-back .content {
    position: absolute;
    top: 0; bottom: 0; left: 51px; right: 0;
    padding: 44px 24px 40px 28px;
    display: flex;
    flex-direction: column;
  }
  .card-back .wordmark { font-size: 26px; }
  .holder { margin-top: 180px; }
  .holder-name {
    font-family: "Josefin Sans", "Century Gothic", sans-serif;
    font-weight: 300;
    font-size: 21px;
    letter-spacing: 0.14em;
    text-transform: uppercase;
    color: var(--ink);
  }
  .holder-role {
    font-family: "Jost", sans-serif;
    font-size: 14px;
    color: var(--accent-red);
    margin-top: 2px;
  }
  .address {
    font-family: "Jost", sans-serif;
    font-size: 12px;
    line-height: 1.35;
    color: var(--ink-soft);
    margin-top: 44px;
  }
  .contact-list { list-style: none; margin-top: 10px; }
  .contact-list li {
    display: flex;
    align-items: center;
    gap: 10px;
    font-family: "Jost", sans-serif;
    font-size: 15px;
    color: var(--ink);
    line-height: 1.45;
  }
  .contact-list li.web { font-weight: 500; }
  .contact-list svg { width: 13px; height: 13px; flex: none; }
</style>
</head>
<body>
  <section class="card card-front">
    <div class="wordmark">Corvane</div>
  </section>

  <section class="card card-back">
    <div class="side-band"></div>
    <div class="side-stripe"></div>
    <div class="content">
      <div class="wordmark">Corvane</div>
      <div class="holder">
        <div class="holder-name">Edmund Calloway</div>
        <div class="holder-role">chairman</div>
      </div>
      <p class="address">14 Ledger Row, EC3N 2LP<br>London, United Kingdom</p>
      <ul class="contact-list">
        <li class="phone">
          <svg viewBox="0 0 16 16" aria-hidden="true"><path fill="#d2331d" d="M1 6c0-2 3-3 7-3s7 1 7 3l-.5 1.5-3-.8V5.5C10 5 6 5 4.5 5.5v1.2l-3 .8zM4 9h8l1 4H3z"/><circle cx="8" cy="11" r="1.3" fill="#fff"/></svg>
          +4420 7946 0831
        </li>
        <li class="email">
          <svg viewBox="0 0 16 16" aria-hidden="true"><rect x="1" y="3" width="14" height="10" fill="#d2331d"/><path d="M1.5 3.5 8 9l6.5-5.5" stroke="#fff" stroke-width="1.3" fill="none"/></svg>
          e@marlowvane.com
        </li>
        <li class="web">
          <svg viewBox="0 0 16 16" aria-hidden="true"><circle cx="8" cy="8" r="6.5" fill="none" stroke="#d2331d" stroke-width="1.5"/><ellipse cx="8" cy="8" rx="2.6" ry="6.5" fill="none" stroke="#d2331d" stroke-width="1.2"/><path d="M1.5 8h13M2.5 5h11M2.5 11h11" stroke="#d2331d" stroke-width="1.1"/></svg>
          www.marlowvane.com
        </li>
      </ul>
    </div>
  </section>
</body>
</html>
```